Dietary supplement, Clean and simple.

Hi,
I’d like to talk about the project,

About us:
We are a dietary supplement (Vitamins, Minerals, amino acids etc.) company.
The goal is to have about 25 products at the end of this year. However, for this goal to be achieved we need a good label design to make our products represent our company values.
I’ll be here every day supporting your questions, we are fully committed to making the highest/best quality/customer experience possible.

About the design and our values:
- Professional (We are in the industry of professionalism and expertise. I would love to show we are competent at this, Id. Like to have the labels looks like we have done our research.)
- Efficient (White spacing, good use of the space available.)
- Simple (Straight forward, in 5 seconds they have to know what the product they have is/how functions. We’re trying to simplify it for the consumer.
- No distractions (the only visually “distracting” factor can be the vector art.)

The guidelines:
The goal is to have a universal design, with one element that changes (Vector art). I’ll attach a file/multiple files I think can show some visuals on what I’m looking for, and what parts of the design I think are good/bad.

Label size: 69x155mm (Front is 77.5mm)

Design whatever you think fits our image. You’re the design expert, all I care about is that it fits our company standards/image.

Use this color/font.
Font: Sans Serif
Main company color is Mind green #237D62 (Use this color for something in the design.)

What I thought would be cool/might looks ugly, who knows:
1. The front of the label: Should have 1 vector art, preferably in the top right corner. (That looks good in multiple colors. The vector can have multiple areas to color, I would prefer 2 main colors in the vector art. The interchangeable colors are used for multiple kinds of products.)
2. Text/product information on the left. The text that will have to be displayed:
- Product name for instance “Magnesium + B6”
- Description for the product for instance “Magnesium with ginger taste”
- Company name or logo. (Add ® behind it. We are soon to be trademark registered.)
3. We need to show the "daily intake" amount on the front and also the amount in the complete bottle. For instance, “Daily intake 1 capsule, 60 capsules”.
• You don’t have to design the backside of the label. After I chose a design, I’d like to chat and give specific information on what areas need to be assigned where. (Too complex because of the law.)
Updates

Hi, Please make the deadline 31 days total. I want designers to have the time to design. And not be rushed to finish it.

I want to extend the deadline because i feel like a slightly more medical look would be interesting. Hope you can come up with something!!

Target Market(s)

Dietary supplement consumers

Industry/Entity Type

Dietary supplements

Font styles to use
Sans Serif

Colors

Designer to choose colors to be used in the design.

Requirements
Must have
• Trademark icon "®" has to be at the top right after the company logo(text of logo)/name.

```html
<!DOCTYPE html>
<html lang="en">
<head>
<meta charset="utf-8">
<title>Magnesium + B6 Label</title>
<link href="https://fonts.googleapis.com/css2?family=Open+Sans:wght@400;600;700&display=swap" rel="stylesheet">
<style>
  :root {
    --page-bg: #e8e8e8;
    --label-bg: #ffffff;
    --brand-green: #1b7a3e;
    --fresh-green: #b9ec5a;
    --pale-green: #e8fbc8;
    --ink: #1f1f1f;
    --mustard: #d3c22e;
    --teal-pill: #7fb8a6;
    --capsule-green: #5a8f22;
    --capsule-blue: #a9cfe6;
  }
  * { margin: 0; padding: 0; box-sizing: border-box; }
  html, body {
    width: 1200px; height: 1200px; overflow: hidden;
    background: var(--page-bg);
    font-family: "Open Sans", Arial, sans-serif;
  }
  .label {
    position: absolute; left: 75px; top: 365px;
    width: 1051px; height: 470px;
    background: var(--label-bg);
    color: var(--ink);
  }
  .front-panel {
    position: absolute; left: 271px; top: 0;
    width: 505px; height: 470px;
    background:
      radial-gradient(ellipse 120% 80% at 100% 0%, var(--fresh-green) 0%, rgba(214,247,150,0.8) 30%, rgba(232,251,200,0.5) 55%, rgba(255,255,255,0) 80%),
      linear-gradient(180deg, var(--pale-green) 0%, rgba(255,255,255,0) 75%);
  }
  .brand {
    position: absolute; left: 271px; width: 505px; top: 138px;
    text-align: center;
    font-weight: 700; font-size: 40px; letter-spacing: 1px;
    color: var(--brand-green);
  }
  .brand sup { font-size: 14px; vertical-align: 22px; margin-left: 2px; }
  .product-name {
    position: absolute; left: 292px; top: 240px;
    font-weight: 600; font-size: 47px; letter-spacing: -0.5px;
    line-height: 1;
  }
  .product-desc {
    position: absolute; left: 292px; top: 296px;
    height: 28px; padding: 0 9px;
    background: var(--mustard); border-radius: 8px;
    font-size: 20px; line-height: 28px;
  }
  .capsules-icon { position: absolute; left: 628px; top: 338px; }
  .count {
    position: absolute; left: 606px; width: 139px; top: 374px;
    text-align: center; line-height: 1;
  }
  .count-number { display: block; font-weight: 700; font-size: 32px; }
  .count-unit { display: block; font-weight: 700; font-size: 10px; letter-spacing: -0.3px; margin-top: 3px; }
  .daily-intake {
    position: absolute; left: 606px; top: 425px;
    width: 139px; height: 19px;
    background: var(--teal-pill); border-radius: 10px;
    font-weight: 700; font-size: 12.5px; line-height: 19px; text-align: center;
  }
  .category {
    position: absolute; left: 299px; top: 416px;
    font-size: 20px; letter-spacing: 0.2px;
  }
</style>
</head>
<body>
  <div class="label">
    <div class="front-panel"></div>
    <div class="brand">Verdant Calm<sup>®</sup></div>
    <h1 class="product-name">MAGNESIUM + B6</h1>
    <div class="product-desc">Magnesium with ginger taste</div>
    <svg class="capsules-icon" width="90" height="36" viewBox="0 0 90 36" aria-hidden="true">
      <g transform="translate(20 18) rotate(35)">
        <rect x="-18" y="-7" width="36" height="14" rx="7" fill="var(--capsule-green)"/>
        <rect x="-14" y="-5" width="22" height="4" rx="2" fill="#ffffff" opacity="0.35"/>
      </g>
      <g transform="translate(66 16) rotate(-40)">
        <rect x="-18" y="-7" width="36" height="14" rx="7" fill="var(--capsule-blue)"/>
        <rect x="-14" y="-5" width="22" height="4" rx="2" fill="#ffffff" opacity="0.5"/>
      </g>
    </svg>
    <div class="count">
      <span class="count-number">60</span>
      <span class="count-unit">CAPSULES</span>
    </div>
    <div class="daily-intake">Daily intake 1 capsule</div>
    <div class="category">DIETARY SUPPLEMENT</div>
  </div>
</body>
</html>
```